Homemaking training schools needs a Business Card design

Designer, Hello!

No special requirements, good-looking enough.
--------------------------------------------------------------------------

Name: Marcus Dole
Chairman
Tel: 0574-71948263
Mobile: 13857420916
Email: kelvora@mailnest.example
Web: www.prt2019.example
Add: No.258, LanpingJie, BeiyuanQu, Ningbo, Zhejiang

LOGO
Ningbo PRT Homemaking Training School

Target Market(s)

pregnant women, mothers, infants, the elderly and families, including cleaning, cooking, nursing training.

Industry/Entity Type

Business

Contact Information for Business Card

Name: Marcus Dole
Chairman
Tel: 0574-71948263
Mobile: 13857420916
Email: kelvora@mailnest.example
Web: www.prt2019.example

LOGO

Font styles to use
Serif
Sans Serif
Decorative

Requirements
Nice to have
• Feels: clean, specifications, safety, comfort, warmth and happiness.

```html
<!DOCTYPE html>
<html lang="en">
<head>
<meta charset="utf-8">
<title>PingRuiTang Business Card</title>
<link rel="stylesheet" href="https://fonts.googleapis.com/css2?family=Quicksand:wght@400;700&family=Open+Sans:wght@400;700&display=swap">
<style>
  :root {
    --page: #e9e6e2;
    --card-light: #ffffff;
    --card-dark: #2a2a2a;
    --brand-blue: #1f73b7;
    --brand-pink: #e6197f;
    --ink: #2b2b2b;
    --rule: #3a3a3a;
    --rule-light: #e8e8e8;
  }
  * { margin: 0; padding: 0; box-sizing: border-box; }
  html, body { width: 1200px; height: 1000px; overflow: hidden; }
  body { background: var(--page); position: relative; font-family: "Open Sans", Arial, sans-serif; }

  .card {
    position: absolute; left: 265px; width: 665px; height: 397px;
    border-radius: 26px; box-shadow: 0 6px 18px rgba(0,0,0,.18);
  }
  .card--front { top: 73px; background: var(--card-light); }
  .card--back { top: 532px; background: var(--card-dark); }

  .brand { position: absolute; left: 0; width: 100%; text-align: center; }
  .card--front .brand { top: 119px; }
  .card--back .brand { top: 195px; }
  .brand__name {
    font-family: "Quicksand", sans-serif; font-weight: 700; font-size: 58px;
    line-height: 1; color: var(--brand-blue); letter-spacing: -0.3px;
  }
  .brand__tagline {
    display: flex; align-items: center; justify-content: center; gap: 10px;
    margin-top: 8px; font-family: "Quicksand", sans-serif; font-size: 21px;
    color: var(--ink);
  }
  .brand__tagline::before, .brand__tagline::after {
    content: ""; width: 80px; height: 1.5px; background: var(--rule);
  }
  .card--back .brand__tagline { color: #f2f2f2; }
  .card--back .brand__tagline::before, .card--back .brand__tagline::after { background: var(--rule-light); width: 88px; }

  .holder { position: absolute; right: 350px; top: 252px; text-align: right; }
  .holder__name { font-weight: 700; font-size: 22px; color: var(--brand-blue); line-height: 1.1; }
  .holder__role { font-size: 14px; color: var(--brand-pink); line-height: 1.3; }
  .holder__address { margin-top: 10px; font-size: 16px; color: var(--ink); line-height: 1.5; }

  .divider { position: absolute; left: 333px; top: 256px; width: 1.5px; height: 92px; background: var(--ink); }

  .contacts { position: absolute; left: 349px; top: 252px; list-style: none; }
  .contacts li { display: flex; align-items: center; gap: 6px; font-size: 16px; color: var(--ink); height: 24.5px; }
  .contacts svg { width: 14px; height: 14px; fill: var(--brand-blue); flex: none; }

  .web { position: absolute; left: 0; width: 100%; bottom: 28px; text-align: center; font-size: 15px; color: #ededed; letter-spacing: 0.5px; }
</style>
</head>
<body>
  <section class="card card--front">
    <div class="brand">
      <div class="brand__name">PingRuiTang</div>
      <div class="brand__tagline">Training &amp; Services</div>
    </div>

    <div class="holder">
      <div class="holder__name">Marcus Dole</div>
      <div class="holder__role">Chairman</div>
      <div class="holder__address">258, LanpingJie, BeiyuanQu,<br>Ningbo, Zhejiang</div>
    </div>

    <div class="divider"></div>

    <ul class="contacts">
      <li><svg viewBox="0 0 14 14"><path d="M4 0h6a1 1 0 0 1 1 1v12a1 1 0 0 1-1 1H4a1 1 0 0 1-1-1V1a1 1 0 0 1 1-1zm.5 1.5v9h5v-9z"/></svg>0574-71948263</li>
      <li><svg viewBox="0 0 14 14"><path d="M1 5c0-2 3-3 6-3s6 1 6 3v1h-3V4.5H4V6H1zM3 7h8l2 5H1z"/></svg>13857420916</li>
      <li><svg viewBox="0 0 14 14"><path d="M0 3h14v8H0zm1.2 1 5.8 4 5.8-4z"/></svg>kelvora@mailnest.example</li>
      <li><svg viewBox="0 0 14 14"><path d="M7 1a6 6 0 1 0 0 12A6 6 0 0 0 7 1zm0 1.5a4.5 4.5 0 0 1 0 9 4.5 4.5 0 0 1 0-9z"/><circle cx="7" cy="7" r="2.2"/></svg>www.prt2019.example</li>
    </ul>
  </section>

  <section class="card card--back">
    <div class="brand">
      <div class="brand__name">PingRuiTang</div>
      <div class="brand__tagline">Training &amp; Services</div>
    </div>
    <div class="web">www.prt2019.example</div>
  </section>
</body>
</html>
```